creation of a business card design for a company specializing in the creation...

I would like to create a design for a professional business card on a black background and with the company's colors (I am attaching some files: including the logo in horizontal and centered format, I am also attaching a recent project design a T-shirt, this is the one I chose to give you an idea of my preferences.

we are in the process of developing a new website design, it is still in the development phase but it can be viewed at the following address: www.vantrelmo.be to give you other ideas about the company
you will see for yourself the subject of my main activity: company specializing in the construction of stairs

I would like a business card that stands out from the rest with a unique design

here is the informations
Name: Lucien Barthel
Function: Manager
Address: Rue Moulinet du Parc 42
7180 La Louvière
telephone: +32 468 219 804
email: info@rx7p.be
website: rx7p. be
social networks: Facebook, YouTube, TikTok, Instagram

Target Market(s)

customer who wants to have a beautiful staircase built

Industry/Entity Type

contruction d'escalier

Contact Information for Business Card

Adresse. Numero de telephone, site web, le texte : "Createur d'escalier", logo recto-verso, icone des reseaux sociaux

Requirements
Must have
• the mention: Stair creator
Nice to have
• an illustration of a designer staircase
Should not have
• do not distort the logo

```html
<!DOCTYPE html>
<html lang="fr">
<head>
<meta charset="utf-8">
<title>RX7P – Cartes de visite</title>
<link href="https://fonts.googleapis.com/css2?family=Montserrat:wght@400;500;700;800&family=Oswald:wght@600&display=swap" rel="stylesheet">
<style>
  :root {
    --backdrop: #3a3a3a;
    --card: #141414;
    --edge: #5d8fb3;
    --accent: #5f97c4;
    --accent-deep: #2b5370;
    --text: #f2f2f2;
    --muted: #9aa6ae;
  }
  * { box-sizing: border-box; margin: 0; padding: 0; }
  html, body { width: 1200px; height: 801px; overflow: hidden; }
  body {
    background: var(--backdrop);
    font-family: "Montserrat", Arial, sans-serif;
    color: var(--text);
    display: flex;
    align-items: center;
    justify-content: center;
    gap: 50px;
  }
  .card {
    width: 525px;
    height: 300px;
    background: var(--card);
    border-bottom: 3px solid var(--edge);
    box-shadow: 0 12px 30px rgba(0,0,0,.45);
    position: relative;
  }

  /* Recto */
  .card--front { display: flex; }
  .front__brand {
    flex: 0 0 55%;
    display: flex;
    flex-direction: column;
    justify-content: center;
    align-items: center;
    gap: 8px;
  }
  .brand-name {
    font-weight: 700;
    font-size: 46px;
    letter-spacing: 6px;
    color: var(--text);
    display: flex;
    align-items: center;
    gap: 14px;
  }
  .brand-mark {
    width: 34px; height: 34px;
    background: var(--accent);
  }
  .brand-tagline {
    font-size: 10px;
    letter-spacing: 5px;
    color: var(--muted);
    text-transform: uppercase;
    padding-left: 48px;
  }
  .front__divider {
    width: 1px;
    background: var(--accent-deep);
    margin: 40px 0;
  }
  .front__details {
    flex: 1;
    padding: 48px 0 0 26px;
    font-size: 13px;
    line-height: 1.45;
  }
  .person-name {
    color: var(--accent);
    font-weight: 800;
    font-size: 17px;
    text-transform: uppercase;
  }
  .person-role { margin-bottom: 16px; }
  .address { margin-bottom: 16px; }
  .contact-line { display: flex; align-items: center; gap: 8px; }
  .contact-line svg { width: 12px; height: 12px; fill: var(--accent); flex: none; }

  /* Verso */
  .card--back {
    display: flex;
    flex-direction: column;
    align-items: center;
    justify-content: center;
  }
  .badge-title {
    font-family: "Oswald", Impact, sans-serif;
    font-size: 17px;
    letter-spacing: 1px;
    text-transform: uppercase;
    color: var(--text);
  }
  .badge-art {
    width: 150px;
    height: 120px;
    border-radius: 50% 50% 8px 8px;
    background: radial-gradient(circle at 50% 45%, #3d6b8a 0%, #1f3c52 60%, #152836 100%);
    margin: 4px 0 6px;
  }
  .card--back .brand-name { font-size: 38px; }
  .card--back .brand-mark { width: 26px; height: 26px; }
  .back__tagline {
    font-size: 11px;
    letter-spacing: 5px;
    color: var(--accent);
    text-transform: uppercase;
    margin-top: 2px;
  }
  .back__contact {
    display: flex; gap: 12px; align-items: center;
    font-size: 10px; margin-top: 6px;
  }
  .back__contact span { display: flex; align-items: center; gap: 4px; }
  .back__contact svg { width: 10px; height: 10px; fill: var(--accent); }
  .social-row { display: flex; gap: 8px; margin-top: 6px; }
  .social-dot { width: 13px; height: 13px; border-radius: 50%; background: var(--accent); }
</style>
</head>
<body>
  <article class="card card--front">
    <div class="front__brand">
      <div class="brand-name"><span class="brand-mark"></span>RX7P</div>
      <div class="brand-tagline">Original Staircases</div>
    </div>
    <div class="front__divider"></div>
    <div class="front__details">
      <p class="person-name">Lucien Barthel</p>
      <p class="person-role">Manager</p>
      <p class="address">Rue Moulinet du Parc 42<br>7180 La Louvière</p>
      <p class="contact-line"><svg viewBox="0 0 24 24"><path d="M6.6 10.8a15 15 0 0 0 6.6 6.6l2.2-2.2a1 1 0 0 1 1-.25 11.4 11.4 0 0 0 3.6.57 1 1 0 0 1 1 1V20a1 1 0 0 1-1 1A17 17 0 0 1 3 4a1 1 0 0 1 1-1h3.5a1 1 0 0 1 1 1c0 1.25.2 2.45.57 3.57a1 1 0 0 1-.25 1z"/></svg>+32 468 219 804</p>
      <p class="contact-line"><svg viewBox="0 0 24 24"><path d="M2 5h20v14H2zm2 2v.5l8 5 8-5V7l-8 5z"/></svg>info@rx7p.be</p>
      <p class="contact-line"><svg viewBox="0 0 24 24"><path d="M12 2a10 10 0 1 0 0 20 10 10 0 0 0 0-20zm0 2c1 1.5 1.7 3.3 1.9 5H10.1C10.3 7.3 11 5.5 12 4zM4.3 13h3.8c.1 1.9.6 3.7 1.4 5.2A8 8 0 0 1 4.3 13zm0-2a8 8 0 0 1 5.2-6.2A13 13 0 0 0 8.1 11zm7.7 9c-1-1.5-1.7-3.3-1.9-5h3.8c-.2 1.7-.9 3.5-1.9 5zm2.5-1.8c.8-1.5 1.3-3.3 1.4-5.2h3.8a8 8 0 0 1-5.2 5.2zM15.9 11a13 13 0 0 0-1.4-6.2A8 8 0 0 1 19.7 11z"/></svg>rx7p. be</p>
    </div>
  </article>

  <article class="card card--back">
    <p class="badge-title">Créateur d'escalier</p>
    <div class="badge-art" role="img" aria-label="Illustration d'un escalier design suspendu dans un médaillon bleu"></div>
    <div class="brand-name"><span class="brand-mark"></span>RX7P</div>
    <p class="back__tagline">Original Staircases</p>
    <div class="back__contact">
      <span><svg viewBox="0 0 24 24"><path d="M6.6 10.8a15 15 0 0 0 6.6 6.6l2.2-2.2a1 1 0 0 1 1-.25 11.4 11.4 0 0 0 3.6.57 1 1 0 0 1 1 1V20a1 1 0 0 1-1 1A17 17 0 0 1 3 4a1 1 0 0 1 1-1h3.5a1 1 0 0 1 1 1c0 1.25.2 2.45.57 3.57a1 1 0 0 1-.25 1z"/></svg>0468 219 804</span>
      <span><svg viewBox="0 0 24 24"><circle cx="12" cy="12" r="10"/></svg>RX7P.BE</span>
    </div>
    <div class="social-row">
      <span class="social-dot"></span><span class="social-dot"></span><span class="social-dot"></span><span class="social-dot"></span>
    </div>
  </article>
</body>
</html>
```